Web Developer Wordpress theme

I'm a web developer but a poor designer so i need somebody to design me a cool and professional WordPress theme. I specialize in shopping cart developments and modifications as well as hosting for these system so would like the design to show this off. I am UK based and want this to also come across in the design.
As for colors and layout i am open mined just use your imaginantion i will let know what i think of your designs.
also forgot to mention my business name is valtrique
and my exsiting site is valtrique.co.uk

```html
<!DOCTYPE html>
<html lang="en">
<head>
<meta charset="utf-8">
<title>Valtrique – Serious Web Development</title>
<link rel="stylesheet" href="https://fonts.googleapis.com/css2?family=Ubuntu:wght@400;500&display=swap">
<style>
  :root {
    --sidebar-bg: #2a2a2a;
    --brand-bg: #242424;
    --nav-line-dark: #1b1b1b;
    --nav-line-light: #4a4a4a;
    --white: #ffffff;
    --accent-orange: #f29a1e;
    --accent-yellow: #f6d630;
    --heading-blue: #1e5f91;
    --body-text: #4a4a4a;
    --footer-blue: #1497c0;
    --input-bg: #eef3ee;
    --input-text: #555555;
    --hero-start: #f4f7f4;
    --hero-end: #e8efe8;
  }
  * { margin: 0; padding: 0; box-sizing: border-box; }
  html, body { width: 1200px; height: 977px; overflow: hidden; }
  body {
    position: relative;
    background: var(--white);
    font-family: "Ubuntu", Tahoma, sans-serif;
    color: var(--body-text);
  }
  .sidebar {
    position: absolute; left: 0; top: 0;
    width: 322px; height: 900px;
    background: var(--sidebar-bg);
  }
  .brand {
    position: absolute; left: 18px; top: 88px;
    width: 286px; height: 88px;
    display: flex; align-items: center; gap: 10px;
    padding-left: 16px;
    background: var(--brand-bg);
  }
  .brand-mark { width: 22px; height: 22px; border-radius: 50%; background: var(--accent-orange); }
  .brand-name { font-size: 44px; font-weight: 500; color: var(--accent-orange); letter-spacing: -0.5px; }
  .main-nav { position: absolute; left: 0; top: 179px; width: 322px; list-style: none; }
  .main-nav li {
    height: 57px;
    border-top: 1px solid var(--nav-line-light);
    border-bottom: 1px solid var(--nav-line-dark);
    display: flex; align-items: center;
    padding-left: 64px;
    color: var(--white); font-size: 17px; text-transform: uppercase;
  }
  .main-nav li:nth-child(3), .main-nav li:nth-child(4) { height: 55px; }
  .newsletter-intro {
    position: absolute; left: 29px; top: 535px; width: 260px;
    color: var(--accent-orange); font-size: 17px; line-height: 20px;
  }
  .field {
    position: absolute; left: 27px; width: 244px; height: 33px;
    background: var(--input-bg);
    font-size: 14px; color: var(--input-text);
    padding: 8px 0 0 19px;
  }
  .field-name { top: 620px; }
  .field-email { top: 667px; }
  .subscribe-button {
    position: absolute; left: 210px; top: 728px;
    width: 62px; height: 58px;
    background: var(--accent-yellow);
    border-radius: 3px;
  }
  .social { position: absolute; left: 162px; top: 825px; display: flex; gap: 4px; }
  .social span { width: 19px; height: 19px; border-radius: 2px; }
  .login {
    position: absolute; left: 1077px; top: 64px;
    color: var(--accent-orange); font-size: 14px; letter-spacing: 0.5px;
  }
  .hero {
    position: absolute; left: 322px; top: 100px;
    width: 850px; height: 418px;
    background: radial-gradient(ellipse at 60% 35%, #f2b53a 0%, #cc4d8f 22%, #1d8f8a 40%, #9cc73f 55%, var(--hero-start) 75%), linear-gradient(180deg, var(--hero-start), var(--hero-end));
    box-shadow: 2px 3px 5px rgba(0,0,0,0.35);
  }
  .content { position: absolute; left: 347px; top: 538px; width: 797px; }
  .content h2 {
    font-size: 17px; font-weight: 400; color: var(--heading-blue);
    margin-bottom: 10px; text-transform: uppercase;
  }
  .content p {
    font-size: 13px; line-height: 17px; margin-bottom: 16px;
    text-align: justify; letter-spacing: 0.3px; hyphens: auto;
  }
  .content section + section { margin-top: 40px; }
  .site-footer {
    position: absolute; left: 0; top: 900px; width: 1200px; height: 77px;
    background: var(--footer-blue);
  }
  .copyright {
    position: absolute; right: 10px; top: 23px;
    color: var(--white); font-size: 13px; font-weight: 500;
  }
</style>
</head>
<body>
  <aside class="sidebar">
    <div class="brand">
      <span class="brand-mark"></span>
      <span class="brand-name">valtrique</span>
    </div>
    <ul class="main-nav">
      <li>Home</li>
      <li>Services</li>
      <li>Addons</li>
      <li>Our E-Commerce Hosting</li>
      <li>Blog</li>
      <li>Contact</li>
    </ul>
    <p class="newsletter-intro">Join our newsletter for all the latest free themes, updates and resources!</p>
    <div class="field field-name">first name</div>
    <div class="field field-email">email address</div>
    <div class="subscribe-button" role="img" aria-label="Subscribe button illustration"></div>
    <div class="social">
      <span style="background:#4b88b9"></span>
      <span style="background:#d23a7a"></span>
      <span style="background:#3fb0e0"></span>
      <span style="background:#2a9ed8"></span>
      <span style="background:#5aa845"></span>
    </div>
  </aside>

  <a class="login">LOGIN HERE</a>

  <div class="hero" role="img" aria-label="Colourful swirling floral illustration with the words design services"></div>

  <main class="content">
    <section>
      <h2>About Us</h2>
      <p>Freelance web developer avaliable for hire, Specializing in Cartwell shopping cart and creating addons and customized templates. I have been a freelance developer for over 5 years now and complete all sizes of projects starting out on HireCodeHub doing small project then going on to the larger projects.</p>
      <p>We create addon and modules to work with the Cartwell shopping cart system. If you just want a new payment gateway or more detailed reports Just ask and we will help.</p>
    </section>
    <section>
      <h2>Our Services</h2>
      <p>Freelance web developer avaliable for hire, Specializing in Cartwell shopping cart and creating addons and customized templates. I have been a freelance developer for over 5 years now and complete all sizes of projects starting out on HireCodeHub doing small project then going on to the larger projects.</p>
      <p>We create addon and modules to work with the Cartwell shopping cart system. If you just want a new payment gateway or more detailed reports Just ask and we will help.</p>
    </section>
  </main>

  <footer class="site-footer">
    <p class="copyright">Website content Copyrighted Valtrique 2011 By: Nordwell Themes</p>
  </footer>
</body>
</html>
```